Homemaking training schools needs a Business Card design

Designer, Hello!

No special requirements, good-looking enough.
--------------------------------------------------------------------------

Name: Marcus Dole
Chairman
Tel: 0574-71948263
Mobile: 13857420916
Email: kelvora@mailnest.example
Web: www.prt2019.example
Add: No.258, LanpingJie, BeiyuanQu, Ningbo, Zhejiang

LOGO
Ningbo PRT Homemaking Training School

Target Market(s)

pregnant women, mothers, infants, the elderly and families, including cleaning, cooking, nursing training.

Industry/Entity Type

Business

Contact Information for Business Card

Name: Marcus Dole
Chairman
Tel: 0574-71948263
Mobile: 13857420916
Email: kelvora@mailnest.example
Web: www.prt2019.example

LOGO

Font styles to use
Serif
Sans Serif
Decorative

Requirements
Nice to have
• Feels: clean, specifications, safety, comfort, warmth and happiness.

```html
<!DOCTYPE html>
<html lang="en">
<head>
<meta charset="utf-8">
<title>PeiRuiTang Business Card</title>
<link href="https://fonts.googleapis.com/css2?family=Lato:wght@400;700&family=Quicksand:wght@400;500&display=swap" rel="stylesheet">
<style>
  :root {
    --bg: #3a3a3c;
    --card: #1c1c1e;
    --blue: #3a7bc8;
    --white: #f4f4f4;
  }
  * { margin: 0; padding: 0; box-sizing: border-box; }
  html, body { width: 1200px; height: 900px; overflow: hidden; background: var(--bg); }
  .stage {
    width: 1200px; height: 900px;
    display: flex; flex-direction: column; align-items: center; justify-content: center; gap: 40px;
  }
  .card {
    position: relative; width: 700px; height: 400px;
    background: var(--card); overflow: hidden;
    box-shadow: 0 12px 30px rgba(0,0,0,.45);
    font-family: 'Lato', sans-serif; color: var(--white);
  }
  .card::after {
    content: ""; position: absolute; left: 0; right: 0; bottom: 0; height: 10px; background: var(--blue);
  }
  .brand { display: flex; flex-direction: column; align-items: center; }
  .brand-name {
    font-family: 'Lato', sans-serif; font-weight: 700; color: var(--white); line-height: 1;
  }
  .brand-tagline {
    display: flex; align-items: center; gap: 12px;
    font-family: 'Quicksand', sans-serif; color: var(--white); white-space: nowrap;
  }
  .brand-tagline::before, .brand-tagline::after {
    content: ""; height: 1.5px; background: var(--white); display: block;
  }

  /* logo side */
  .card-front .brand { position: absolute; left: 0; right: 0; top: 112px; }
  .card-front .brand-name { font-size: 64px; }
  .card-front .brand-tagline { font-size: 22px; margin-top: 14px; }
  .card-front .brand-tagline::before, .card-front .brand-tagline::after { width: 95px; }
  .card-front .website {
    position: absolute; left: 0; right: 0; top: 278px; text-align: center;
    font-family: 'Quicksand', sans-serif; font-size: 17px; letter-spacing: 3px;
  }

  /* contact side */
  .card-back .brand { position: absolute; left: 38px; top: 40px; align-items: flex-start; }
  .card-back .brand-name { font-size: 42px; }
  .card-back .brand-tagline { font-size: 15px; margin-top: 8px; }
  .card-back .brand-tagline::before, .card-back .brand-tagline::after { width: 55px; }
  .person { position: absolute; right: 60px; top: 102px; text-align: right; }
  .person-name { font-size: 30px; color: var(--blue); }
  .person-title { font-size: 19px; margin-top: 2px; }
  .divider {
    position: absolute; left: 140px; right: 60px; top: 172px; height: 1.5px; background: var(--white);
  }
  .contacts { position: absolute; left: 40px; top: 200px; list-style: none; }
  .contacts li { display: flex; align-items: center; gap: 14px; font-size: 19px; line-height: 29px; }
  .contacts svg { width: 16px; height: 16px; fill: var(--blue); flex: none; }
  .address {
    position: absolute; right: 60px; top: 292px; text-align: right; font-size: 21px; line-height: 29px;
  }
</style>
</head>
<body>
<main class="stage">
  <section class="card card-front">
    <div class="brand">
      <p class="brand-name">PeiRuiTang</p>
      <p class="brand-tagline">Training &amp; Services</p>
    </div>
    <p class="website">www.prt2019.example</p>
  </section>

  <section class="card card-back">
    <div class="brand">
      <p class="brand-name">PeiRuiTang</p>
      <p class="brand-tagline">Training &amp; Services</p>
    </div>
    <div class="person">
      <p class="person-name">Marcus Dole</p>
      <p class="person-title">Chairman</p>
    </div>
    <div class="divider"></div>
    <ul class="contacts">
      <li><svg viewBox="0 0 16 16" aria-hidden="true"><path d="M3.5 1 6 1.5 7 5 5.3 6.3c.8 1.8 2.3 3.4 4.4 4.4L11 9l3.5 1 .5 2.5-2 2C6.5 14.5 1.5 9.5 1.5 3z"/></svg>0574-71948263</li>
      <li><svg viewBox="0 0 16 16" aria-hidden="true"><path d="M4.5 1h7a1 1 0 0 1 1 1v12a1 1 0 0 1-1 1h-7a1 1 0 0 1-1-1V2a1 1 0 0 1 1-1zm.5 2v9h6V3zm3 10a.8.8 0 1 0 0 .01z"/></svg>1385-7420916</li>
      <li><svg viewBox="0 0 16 16" aria-hidden="true"><path d="M1 3.5h14v9H1zm1.3 1 5.7 4.3 5.7-4.3z"/></svg>kelvora@mailnest.example</li>
      <li><svg viewBox="0 0 16 16" aria-hidden="true"><path d="M8 1a7 7 0 1 0 0 14A7 7 0 0 0 8 1zm-.7 1.6v2.6H5a7 7 0 0 1 2.3-2.6zm1.4 0A7 7 0 0 1 11 5.2H8.7zM3 7.3h4.3v1.4H3zm5.7 0H13v1.4H8.7zM5 10.8h2.3v2.6A7 7 0 0 1 5 10.8zm3.7 0H11a7 7 0 0 1-2.3 2.6z"/></svg>www.prt2019.example</li>
    </ul>
    <p class="address">No.258, LanpingJie<br>BeiyuanQu, Ningbo, Zhejiang</p>
  </section>
</main>
</body>
</html>
```